Thoroughbred Racing Partnership needs web design

Glimmer of Laurel Partners is a management group who buys horses and races them on both the West and East coasts. The premise of the business is for an investment as little as $500, anyone can be a partner and own a percentage of a horse(s). This is a low cost way of getting involved in the exciting sport of Thoroughbred Racing, without shouldering the heavy financial responsibility. Our target market is mostly males 40+ but we want to include all target markets. We are looking for something very clean and professional, we want to give an image of success. Nothing overly "artsy." I have included the logo in which you can incorporate in the site. Also, the logo colors will be the colors of our "silks." The silks are what the jockey wears and will be an important marketing tool for GOL. We would like a very prominent picture of a racehorse somewhere on the homepage, we want to make it clear that is a website for Horseracing partnerships.

On the top of the site, it should say "Glimmer of Laurel" (on the top)
and below that "Thoroughbred Racing Partnerships." (below that)

The main sections, which should be across the top are:

Home
About Us
Ownership
Stable Roster
News
Contact us

Some of these will have drop down menus.

An example of a competitor website that we like is: www.harrowgatefarm.example
An example of a competitor website that we don't like is: www.paddockvue.example
Updates

Project Deadline Extended
Reason: We have a Board of Directors meeting on the 22nd and we will be making a decision on that day. I'm giving an extension so that all designers are able to submit their designs by the 22nd. Thank you!

Target Market(s)

40+ males

Industry/Entity Type

Business

Requirements
Must have
• our logo must be on the site. We would like at least one bold image of a thoroughbred horse in action. The picture is going to tell the story so it needs to be very eye-catching.

Our slogan should also be included on the website, "Experience the thrill of owning a Racehorse."
Should not have
• cartoons, artsy pictures, pictures of Steeplechase horses or "jumpers." This partnership is for racehorses only, there is not jumping involved with the horses.

```html
<!DOCTYPE html>
<html lang="en">
<head>
<meta charset="utf-8">
<title>Glimmer of Laurel Partners</title>
<link href="https://fonts.googleapis.com/css2?family=Open+Sans:wght@400;600;700&family=PT+Sans+Narrow:wght@400;700&family=Roboto:wght@400;700&display=swap" rel="stylesheet">
<style>
:root{
  --navy:#1b3a66;
  --sky-top:#4a78b0;
  --sky-mid:#a9c3dd;
  --field:#8a7a55;
  --nav-dark:#111;
  --nav-active:#5f93b8;
  --dark-1:#141414;
  --dark-2:#232323;
  --rule:#3c3c3c;
  --text-muted:#b8b8b8;
  --accent:#7aa6c7;
  --footer:#0b3c6d;
  --footer-rule:#3d6594;
  --white:#fff;
}
*{margin:0;padding:0;box-sizing:border-box}
html,body{width:1034px;height:1200px;overflow:hidden;background:var(--dark-1)}
body{position:relative;font-family:"Roboto",Arial,sans-serif;color:var(--white)}
.abs{position:absolute}

/* hero */
.hero{left:0;top:0;width:1034px;height:557px;overflow:hidden}
.hero-photo{position:absolute;inset:0;background:
  linear-gradient(90deg,rgba(0,0,0,0) 15%,rgba(70,45,30,.35) 35%,rgba(70,45,30,.35) 65%,rgba(0,0,0,0) 80%),
  linear-gradient(180deg,var(--sky-top) 0%,var(--sky-mid) 45%,#c9cfcf 62%,#a69467 78%,var(--field) 100%)}
.brand-box{left:121px;top:17px;width:158px;height:84px;background:var(--white);display:flex;align-items:center;justify-content:center;gap:6px}
.brand-box .dot{width:12px;height:12px;border-radius:50%;background:var(--navy)}
.brand-box span{font-family:"Open Sans",sans-serif;font-weight:700;font-size:13px;color:var(--navy)}
.tagline{left:672px;top:12px;font-family:"Open Sans",sans-serif;font-weight:600;font-size:11.5px;line-height:20px;color:#e8eef5;text-transform:uppercase;white-space:nowrap}
.main-nav{left:279px;top:61px;width:633px;height:40px;background:linear-gradient(#2a2a2a,var(--nav-dark));border-radius:0 4px 4px 0;display:flex;padding-left:85px}
.main-nav a{font-family:"Open Sans",sans-serif;font-weight:700;font-size:11px;color:var(--white);text-decoration:none;display:flex;align-items:center;justify-content:center;white-space:nowrap;border-right:1px solid #333}
.main-nav a:last-child{border:0}
.main-nav a.active{background:linear-gradient(#7fb0d1,var(--nav-active))}
.slogan{left:123px;top:142px;font-family:"PT Sans Narrow",sans-serif;font-weight:700;font-size:36px;line-height:37px;color:var(--navy)}
.dots{left:831px;top:521px;display:flex;gap:9px}
.dots i{width:13px;height:13px;border-radius:50%;background:#f2f2f2}
.dots i.on{background:#3f7bb0;border:2px solid #fff}

/* welcome */
.welcome{left:0;top:557px;width:1034px;height:233px;background:linear-gradient(90deg,#1a1a1a,#101010)}
.welcome-head{left:122px;top:595px;font-family:"PT Sans Narrow",sans-serif;font-size:20px;color:var(--accent);display:flex;align-items:center;gap:8px}
.welcome-head b{color:var(--white);font-family:"PT Sans Narrow",sans-serif;font-size:24px}
.welcome-rule{left:122px;top:630px;width:465px;height:1px;background:var(--rule)}
.welcome-lead{left:122px;top:638px;font-size:11px;font-weight:700}
.welcome-body{left:122px;top:659px;width:468px;font-size:10.3px;line-height:16px;color:var(--text-muted);text-align:justify}
.more{font-size:10.5px;font-style:italic;color:var(--accent)}
.video{left:613px;top:588px;width:300px;height:182px;border:1px solid #555;background:linear-gradient(#dfe4e8,#b9c2c9)}
.video-name{position:absolute;left:0;right:0;top:82px;text-align:center;font-family:"Open Sans",sans-serif;font-weight:700;font-size:20px;color:var(--navy)}
.video-bar{position:absolute;left:0;right:0;bottom:0;height:28px;background:linear-gradient(#2b2b2b,#111)}

/* columns */
.cols{left:0;top:790px;width:1034px;height:244px;background:var(--dark-2)}
.col{top:806px;width:240px}
.col h2{font-family:"PT Sans Narrow",sans-serif;font-weight:700;font-size:19px;color:var(--white);padding-bottom:4px;border-bottom:1px solid var(--rule)}
.col h2 span{color:var(--accent);font-weight:400}
.col p{font-size:10px;line-height:13.7px;color:var(--text-muted)}
.list{list-style:none;margin-top:16px}
.list li{font-size:9.5px;font-weight:700;line-height:16px;padding-left:14px;position:relative;white-space:nowrap}
.list li::before{content:"»";position:absolute;left:0;color:#888}
.list li.hl{color:var(--accent)}
.event{display:flex;gap:17px;padding:8px 0;border-bottom:1px solid var(--rule)}
.event:last-child{border:0}
.date{width:34px;height:34px;flex:none;background:linear-gradient(#cfcfcf,#9a9a9a);border-radius:3px;color:#333;text-align:center;font-weight:700;font-size:15px;line-height:17px;padding-top:2px}
.date small{display:block;font-size:8px;line-height:9px}
.vr{top:802px;width:1px;height:216px;background:#111;border-right:1px solid #333}
.portrait{left:676px;top:842px;width:65px;height:65px;background:linear-gradient(#e8e8e8,#8d9196)}

/* footer */
.footer{left:0;top:1034px;width:1034px;height:166px;background:var(--footer);border-top:2px solid #3a77aa}
.f-head{font-family:"Open Sans",sans-serif;font-weight:600;font-size:12.5px;padding-bottom:4px;border-bottom:1px solid var(--footer-rule)}
.f-links{list-style:none;font-size:9.5px;line-height:25px}
.f-links li::before{content:"›";font-weight:700;font-size:13px;margin-right:8px}
.f-text{font-size:9.5px;line-height:14px;color:#e6eef7}
.email{width:172px;height:22px;background:#fff;border-radius:2px;color:#777;font-size:9px;padding:5px 7px}
.subscribe{width:68px;height:20px;background:linear-gradient(#8ab4d4,#4f86b2);border-radius:2px;font-size:9px;font-weight:700;text-align:center;line-height:20px}
.social{display:flex;gap:10px}
.social i{width:26px;height:26px;border-radius:50%;background:#9fb3c8}
</style>
</head>
<body>

<section class="abs hero">
  <div class="hero-photo" role="img" aria-label="Photograph of a dark bay thoroughbred in full stride under a rider, with fences and open field under a blue sky"></div>
</section>

<div class="abs brand-box"><i class="dot"></i><span>GOLPARTNERS.COM</span></div>
<div class="abs tagline">Glimmer of Laurel<br>Thoroughbred Racing Partnerships</div>
<nav class="abs main-nav">
  <a class="active" href="#" style="width:69px">HOME</a><a href="#" style="width:91px">ABOUT US</a><a href="#" style="width:101px">OWNERSHIP</a><a href="#" style="width:117px">STABLE ROSTER</a><a href="#" style="width:66px">NEWS</a><a href="#" style="width:104px">CONTACT US</a>
</nav>
<h1 class="abs slogan">Experience the thrill<br>of owning a Racehorse.</h1>
<div class="abs dots"><i class="on"></i><i></i><i></i><i></i></div>

<section class="abs welcome"></section>
<div class="abs welcome-head">Welcome to <b>GOL</b></div>
<div class="abs welcome-rule"></div>
<p class="abs welcome-lead">Glimmer of Laurel Partners is a management group who buys horses and races</p>
<p class="abs welcome-body">Glimmer of Laurel Partners is a management group who buys horses and races them on both the West and East coasts. The premise of the business is for an investment as little as $500, anyone can be a partner and own a percentage of a horse(s). This is a low cost way of getting involved in the exciting sport of Thoroughbred Racing, without shouldering the heavy financial responsibility.</p>
<span class="abs more" style="left:526px;top:755px">Read More »</span>
<div class="abs video">
  <svg class="abs" style="left:136px;top:58px" width="28" height="28" viewBox="0 0 28 28"><circle cx="14" cy="14" r="14" fill="#3a3a3a"/><path d="M11 8l9 6-9 6z" fill="#fff"/></svg>
  <div class="video-name">GOL PARTNERS</div>
  <div class="video-bar">
    <svg width="298" height="28" viewBox="0 0 298 28">
      <rect x="0" y="0" width="298" height="5" fill="#555"/><rect x="0" y="0" width="24" height="5" fill="#c00"/>
      <circle cx="24" cy="3" r="5" fill="#ddd"/>
      <rect x="17" y="11" width="3" height="11" fill="#ddd"/><rect x="23" y="11" width="3" height="11" fill="#ddd"/>
      <path d="M48 14h4l5-4v13l-5-4h-4z" fill="#ddd"/>
      <text x="72" y="20" font-size="8" fill="#fff" font-family="Roboto,sans-serif">0:07 <tspan fill="#aaa">/ 2:54</tspan></text>
      <rect x="230" y="12" width="9" height="7" fill="#ccc"/><circle cx="260" cy="16" r="5" fill="#ccc"/>
      <path d="M276 10v4M276 10h4M290 10h-4M290 10v4M276 23v-4M276 23h4M290 23h-4M290 23v-4" stroke="#ccc" stroke-width="1.5"/>
    </svg>
  </div>
</div>

<section class="abs cols"></section>
<div class="abs col" style="left:122px">
  <h2><span>Shortly</span> About Us</h2>
  <p style="margin-top:8px">Duis autem veli eum iriure dolor in hendrerit in vulputate velit esse molestie consequat, vel illum dolorel feugiatmul nulla facilisis at vero eros et accumsano et iusto odio dignissim qui blandit praesent luptatuli zrilopil delenit augue duis dolore te feugait nullamol facilisi.</p>
  <ul class="list">
    <li>Lorem ipsum dolor sit amet, consectetuer</li>
    <li class="hl">Duis autem veli eum iriure dolor in hendrerit</li>
    <li>Blandit praesent luptatuli zrilopil delenit</li>
  </ul>
</div>
<span class="abs more" style="left:291px;top:1005px">Read More »</span>
<div class="abs vr" style="left:378px"></div>

<div class="abs col" style="left:397px">
  <h2><span>Latest</span> News &amp; Events</h2>
  <div class="event"><div class="date">29<small>OCT</small></div><p>Lorem ipsum dolor sit amet, consectetu adipiscing elit, sed diam nonummy nibh consecte nonummy nibh.</p></div>
  <div class="event"><div class="date">29<small>OCT</small></div><p>Lorem ipsum dolor sit amet, consectetu adipiscing elit, sed diam nonummy nibh consecte nonummy nibh.</p></div>
  <div class="event"><div class="date">29<small>OCT</small></div><p>Lorem ipsum dolor sit amet, consectetu adipiscing elit, sed diam nonummy nibh consecte nonummy nibh.</p></div>
</div>
<span class="abs more" style="left:574px;top:1005px">Read More »</span>
<div class="abs vr" style="left:653px"></div>

<div class="abs col" style="left:672px">
  <h2><span>Client</span> Testimonials</h2>
</div>
<div class="abs portrait" role="img" aria-label="Portrait photo of the quoted client"></div>
<p class="abs" style="left:756px;top:838px;width:156px;font-size:10px;line-height:15.8px;color:var(--text-muted)">“ Ut wisi enim ad mini veniam, quis nostrud exerci tationullamo corper suscipit lobortis nislutalil uip commodoconsequat. ”</p>
<p class="abs" style="left:756px;top:916px;font-size:11px;font-weight:700;color:var(--accent)">Mr. Lorem ipsum sit amet</p>
<p class="abs" style="left:756px;top:933px;font-size:11px;font-weight:700">Chief Executive</p>
<span class="abs more" style="left:849px;top:1005px">Read More »</span>

<footer class="abs footer"></footer>
<div class="abs" style="left:123px;top:1058px;width:204px">
  <h3 class="f-head">QUICK LINKS</h3>
  <div style="display:flex;gap:38px;margin-top:4px">
    <ul class="f-links"><li>Home</li><li>About Us</li><li>Ownership</li><li>Stable Roster</li></ul>
    <ul class="f-links"><li>News</li><li>Contact Us</li></ul>
  </div>
</div>
<div class="abs vr" style="left:347px;top:1058px;height:120px;background:#082c52;border-color:#2a5888"></div>
<div class="abs" style="left:369px;top:1058px;width:178px">
  <h3 class="f-head">NEWSLETTER</h3>
  <p class="f-text" style="margin-top:10px">Subscribe to our newsletter to receive our special offers and more.</p>
  <div class="email" style="margin-top:9px">Enter your Email Address here</div>
  <div class="subscribe" style="margin:7px 0 0 104px">SUBSCRIBE</div>
</div>
<div class="abs vr" style="left:567px;top:1058px;height:120px;background:#082c52;border-color:#2a5888"></div>
<div class="abs" style="left:586px;top:1058px;width:154px">
  <h3 class="f-head">CONTACT DETAILS</h3>
  <div style="display:flex;gap:9px;margin-top:10px"><svg width="10" height="14" viewBox="0 0 10 14"><path d="M5 0a5 5 0 0 1 5 5c0 4-5 9-5 9S0 9 0 5a5 5 0 0 1 5-5z" fill="#fff"/><circle cx="5" cy="5" r="2" fill="#0b3c6d"/></svg><p class="f-text">Sed diam nonummy euismod tincidunt ut laor</p></div>
  <div style="display:flex;gap:9px;margin-top:14px;align-items:center"><svg width="12" height="12" viewBox="0 0 12 12"><path d="M2 0h3l1 3-2 1.5a7 7 0 0 0 3.5 3.5L9 6l3 1v3a2 2 0 0 1-2 2A10 10 0 0 1 0 2a2 2 0 0 1 2-2z" fill="#fff"/></svg><p class="f-text">(000)123-4567</p></div>
  <div style="display:flex;gap:9px;margin-top:16px;align-items:center"><svg width="12" height="9" viewBox="0 0 12 9"><rect width="12" height="9" fill="#fff"/><path d="M0 0l6 5 6-5" stroke="#0b3c6d" fill="none"/></svg><p class="f-text">info@golpartners.example</p></div>
</div>
<div class="abs vr" style="left:760px;top:1058px;height:120px;background:#082c52;border-color:#2a5888"></div>
<div class="abs" style="left:780px;top:1066px;width:134px;text-align:center">
  <p style="font-family:'Open Sans',sans-serif;font-weight:700;font-size:13px;color:#c9d6e4">GOLPARTNERS.COM</p>
  <p class="f-text" style="margin-top:18px">Copyright © 2013 Gol.</p>
</div>
<div class="abs social" style="left:780px;top:1151px" role="img" aria-label="Social network links">
  <i></i><i></i><i></i><i></i>
</div>

</body>
</html>
```